Wellness, Meaning, and the Inner Journey Research Program Website

Overview: This website will serve a new research program (Wellness, Meaning, and the Inner Journey) at the Harrowgate University School of Medicine. I want a clean, intuitive design that has a navigation bar, but uses icons/graphic buttons to link to the main pages. In an attached Word document, I have provided a basic information architecture for the site, understanding that this project would just generate graphics and code for the 3 pages. I highlighted the 3 pages I'd like designed.
Target market: People who want to participate in our research, or contribute grant funding to specific projects.
Number of page: The design project focuses on 3 pages, but the site must accommodate 6 pages with top-level links. See attached Word doc.
Logo and website header: Please integrate our logo in the header. I've uploaded it as a png file--both with the name of the website and with just the logo image. I imaging the logo would look great in a banner set against an image of a mountain. The two main design themes I want to see included are nature and healthcare.
Text content: I have not yet provided text. Use some dummy text.
Technical Specifications:
- Build using WordPress. We will host this site ourselves on NetHarbor using WordPress.
- The design package must be coded.
- The template must be responsive to different platforms (e.g., computer, mobile phone, iPad).
Thank you! I look forward to seeing your designs.
- Ned

```html
<!DOCTYPE html>
<html lang="en">
<head>
<meta charset="utf-8">
<title>Wellness, Meaning, and the Inner Journey — The Research Program</title>
<link href="https://fonts.googleapis.com/css2?family=Ubuntu:wght@400;500;700&family=Roboto:wght@400;500&display=swap" rel="stylesheet">
<style>
:root{
  --night:#05080c;
  --navy:#124480;
  --green:#44912d;
  --teal:#17674f;
  --ink:#2b2b2b;
  --muted:#555;
  --white:#fff;
  --line:#c9c9c9;
  --footer:#124480;
}
*{box-sizing:border-box;margin:0;padding:0}
html,body{width:1200px;height:2411px;overflow:hidden}
body{position:relative;font-family:"Ubuntu",sans-serif;color:var(--ink);background:#f4f1ee}
.page-bg{position:absolute;left:0;top:630px;width:1200px;height:1665px;
  background:linear-gradient(180deg,#f6f8fa 0%,#e6ecef 18%,#d9dde0 40%,#e3e0dc 60%,#f4ece6 75%,#ecebf0 100%)}
.hero{position:absolute;left:0;top:0;width:1200px;height:630px;
  background:linear-gradient(180deg,#05080c 0%,#0b0f14 22%,#5b3a2e 36%,#7a5a4a 46%,#3b4030 60%,#2a3a3a 80%,#4a6a6a 100%)}
.header{position:absolute;left:0;top:0;width:1200px;height:112px}
.brand{position:absolute;left:112px;top:34px;display:flex;align-items:center;gap:12px}
.brand-dot{width:44px;height:44px;border-radius:50%;background:var(--green)}
.brand-name{font-weight:500;font-size:14px;line-height:17px;color:#3f86c7}
.nav{position:absolute;right:112px;top:48px;display:flex;gap:44px}
.nav a{color:var(--white);text-decoration:none;font-size:13px}
.hero-title{position:absolute;left:0;top:276px;width:1200px;text-align:center;color:var(--white);
  font-weight:500;font-size:38px;letter-spacing:.5px}
.hero-sub{position:absolute;left:0;top:323px;width:1200px;text-align:center;color:var(--white);font-weight:500;font-size:31px}
.circle{position:absolute;border-radius:50%;background:var(--white);box-shadow:0 14px 30px rgba(0,0,0,.15)}
.circle-inner{position:absolute;border-radius:50%;display:flex;flex-direction:column;align-items:center;text-align:center;color:var(--white)}
.circle h2{font-weight:500;font-size:21px;letter-spacing:.3px}
.circle h2::after{content:"";display:block;width:56px;height:1px;background:var(--white);margin:7px auto 0}
.circle p{font-size:13px;line-height:19px;margin-top:10px;width:262px}
.circle .btn{margin-top:23px;background:var(--white);padding:9px 20px;font-size:13px;font-weight:500;border-radius:2px}
.section-title{font-weight:700;color:#333;font-size:30px}
.projects-title{position:absolute;left:0;top:910px;width:1200px;text-align:center}
.projects-lede{position:absolute;left:0;top:948px;width:1200px;text-align:center;font-size:16px;line-height:25px;color:var(--muted)}
.card{position:absolute;top:1020px;width:314px;height:289px;border-radius:2px;overflow:hidden}
.card span{position:absolute;left:20px;bottom:18px;color:var(--white);font-size:21px;font-weight:500}
.card::after{content:"";position:absolute;left:0;right:0;bottom:0;height:90px;background:linear-gradient(transparent,rgba(0,0,0,.75))}
.card span{z-index:1}
.faq-title{position:absolute;left:110px;top:1404px}
.faq-item{position:absolute;left:111px;width:554px;height:55px;background:var(--white);border:1px solid #dcdcdc;
  box-shadow:0 2px 4px rgba(0,0,0,.15);display:flex;align-items:center;justify-content:space-between;padding:0 24px;font-size:14px;font-weight:500;color:#222}
.faq-item svg{flex:none}
.res-title{position:absolute;left:728px;top:1404px}
.res-card{position:absolute;left:728px;top:1470px;width:360px;height:254px;background:linear-gradient(160deg,#1a1a1a 0%,#3a1517 45%,#123a36 100%)}
.res-card span{position:absolute;left:20px;bottom:20px;color:var(--white);font-size:19px;line-height:29px;width:300px}
.contact-title{position:absolute;left:107px;top:1845px;font-size:38px}
.contact-lede{position:absolute;left:111px;top:1902px;font-size:13px;line-height:20px;color:var(--muted);width:420px}
.info{position:absolute;left:127px;display:flex;gap:14px}
.info h3{font-family:"Roboto",sans-serif;font-weight:500;font-size:15px;color:var(--navy)}
.info p{font-size:12px;line-height:23px;margin-top:6px;color:#333}
.socials{position:absolute;left:148px;top:2184px;display:flex;gap:11px}
.socials span{width:33px;height:33px;border-radius:50%;display:block}
.map{position:absolute;left:423px;top:1969px;width:301px;height:251px;background:#efe3cd;box-shadow:0 2px 6px rgba(0,0,0,.3)}
.form{position:absolute;left:792px;top:1960px;width:295px;font-family:"Roboto",sans-serif}
.field{height:30px;border-bottom:1px solid var(--line);font-size:12px;color:#555;padding-top:6px;margin-bottom:26px}
.submit{position:absolute;left:131px;top:212px;width:163px;height:45px;background:var(--navy);color:var(--white);
  font-size:14px;display:flex;align-items:center;justify-content:center;box-shadow:0 2px 6px rgba(0,0,0,.25)}
.footer{position:absolute;left:0;top:2295px;width:1200px;height:116px;background:var(--footer)}
.footer nav{position:absolute;left:112px;top:48px;display:flex;gap:44px}
.footer a,.footer .copy{color:var(--white);text-decoration:none;font-size:13px}
.footer .copy{position:absolute;right:113px;top:48px}
</style>
</head>
<body>
<div class="page-bg" role="img" aria-label="Faded mountain lake landscape with city skyline at the bottom"></div>

<section class="hero" role="img" aria-label="Mountain range at dusk above a calm lake">
  <header class="header">
    <div class="brand"><span class="brand-dot"></span><span class="brand-name">Wellness, Meaning, and the Inner Journey<br>The Research Program</span></div>
    <nav class="nav"><a href="#">Home</a><a href="#">People</a><a href="#">Research Projects</a><a href="#">FAQs</a><a href="#">Resources</a><a href="#">Contact</a></nav>
  </header>
  <h1 class="hero-title">Wellness, Meaning, and the Inner Journey</h1>
  <p class="hero-sub">The Research Program</p>
</section>

<div class="circle" style="left:101px;top:426px;width:356px;height:356px">
  <div class="circle-inner" style="left:9px;top:9px;width:338px;height:338px;background:var(--green);padding-top:86px">
    <h2>RESEARCH TEAM</h2>
    <p>Lorem Ipsum is simply dummy text of the printing and typesetting industry. Lorem Ipsum has been the industry's standard dummy text ever since the 1500s</p>
    <span class="btn" style="color:var(--green)">Learn More</span>
  </div>
</div>
<div class="circle" style="left:733px;top:426px;width:356px;height:356px">
  <div class="circle-inner" style="left:9px;top:9px;width:338px;height:338px;background:var(--teal);padding-top:86px">
    <h2>PARTNERS</h2>
    <p>Lorem Ipsum is simply dummy text of the printing and typesetting industry. Lorem Ipsum has been the industry's standard dummy text ever since the 1500s</p>
    <span class="btn" style="color:var(--teal)">Learn More</span>
  </div>
</div>
<div class="circle" style="left:404px;top:408px;width:392px;height:392px">
  <div class="circle-inner" style="left:11px;top:11px;width:370px;height:370px;background:var(--navy);padding-top:95px">
    <h2>ADVISORY COMMITTEE</h2>
    <p>Lorem Ipsum is simply dummy text of the printing and typesetting industry. Lorem Ipsum has been the industry's standard dummy text ever since the 1500s</p>
    <span class="btn" style="color:var(--navy)">Learn More</span>
  </div>
</div>

<h2 class="section-title projects-title">PROJECTS</h2>
<p class="projects-lede">Lorem Ipsum is simply dummy text of the printing and<br>Lorem Ipsum has been the industry's standard dummy text ever since the 1500s</p>
<div class="card" style="left:111px;background:linear-gradient(160deg,#8fa2b4,#35485a 60%,#1b2632)" role="img" aria-label="Two researchers reviewing documents in a lab"><span>Neque porro quisquam</span></div>
<div class="card" style="left:443px;background:radial-gradient(circle at 56% 60%,#d9b070 0%,#3a4a55 25%,#141c28 70%)" role="img" aria-label="Two glowing hands reaching toward each other in space"><span>Neque porro quisquam</span></div>
<div class="card" style="left:775px;background:linear-gradient(180deg,#6c6f8c 0%,#c7808a 35%,#e0703a 55%,#3a2a2a 100%)" role="img" aria-label="Meditating figure silhouetted against a sunset"><span>Neque porro quisquam</span></div>

<h2 class="section-title faq-title">FAQ</h2>
<div class="faq-item" style="top:1470px">What makes this project unique?<svg width="16" height="16" viewBox="0 0 16 16"><circle cx="8" cy="8" r="8" fill="#222"/><path d="M8 4v8M4 8h8" stroke="#fff" stroke-width="2"/></svg></div>
<div class="faq-item" style="top:1535px;font-size:13px">Does this project assume that the impact of religion is always positive?<svg width="16" height="16" viewBox="0 0 16 16"><circle cx="8" cy="8" r="8" fill="#222"/><path d="M8 4v8M4 8h8" stroke="#fff" stroke-width="2"/></svg></div>
<div class="faq-item" style="top:1600px">How can I collaborate?<svg width="16" height="16" viewBox="0 0 16 16"><circle cx="8" cy="8" r="8" fill="#222"/><path d="M8 4v8M4 8h8" stroke="#fff" stroke-width="2"/></svg></div>
<div class="faq-item" style="top:1665px">Will Harrowgate faculty lead all projects?<svg width="16" height="16" viewBox="0 0 16 16"><circle cx="8" cy="8" r="8" fill="#222"/><path d="M8 4v8M4 8h8" stroke="#fff" stroke-width="2"/></svg></div>

<h2 class="section-title res-title">RESOURCES</h2>
<div class="res-card" role="img" aria-label="Person in a suit touching a glowing data chart"><span>Neque porro quisquam est qui dolorem ipsum</span></div>

<h2 class="section-title contact-title">CONTACT US</h2>
<p class="contact-lede">Sed ut perspiciatis unde omnis iste natus error sit voluptatem accusantium doloremque laudantium, totam rem aperiam,</p>

<div class="info" style="top:1967px">
  <svg width="14" height="18" viewBox="0 0 14 18"><path d="M7 0a7 7 0 0 0-7 7c0 5 7 11 7 11s7-6 7-11a7 7 0 0 0-7-7z" fill="var(--navy)"/><circle cx="7" cy="7" r="2.5" fill="#fff"/></svg>
  <div><h3>Address</h3><p>742 Larkspur Lane, Fernhollow,<br>CO, 80555.</p></div>
</div>
<div class="info" style="top:2051px">
  <svg width="16" height="16" viewBox="0 0 16 16"><path d="M3 0l3 4-2 2c1 2 4 5 6 6l2-2 4 3-2 3C7 16 0 9 0 3z" fill="var(--navy)"/></svg>
  <div><h3>Phone</h3><p>555-210-4387</p></div>
</div>
<div class="info" style="top:2116px">
  <svg width="16" height="12" viewBox="0 0 16 12"><rect width="16" height="12" rx="1" fill="var(--navy)"/><path d="M1 1l7 6 7-6" stroke="#fff" stroke-width="1.4" fill="none"/></svg>
  <div><h3>Email</h3><p>hello@innerjourney.org</p></div>
</div>
<div class="socials" aria-label="Social links">
  <span style="background:#1a6fb0"></span><span style="background:#d32020"></span><span style="background:#2a5aa8"></span><span style="background:#2f9de0"></span>
</div>

<div class="map" role="img" aria-label="Location map of the office area"></div>

<form class="form">
  <div class="field">First Name</div>
  <div class="field">Phone</div>
  <div class="field">Email</div>
  <div class="field">Message Here</div>
  <div class="submit">SUBMIT NOW</div>
</form>

<footer class="footer">
  <nav><a href="#">Home</a><a href="#">People</a><a href="#">Research Projects</a><a href="#">FAQs</a><a href="#">Resources</a><a href="#">Contact</a></nav>
  <span class="copy">WMIJ © 2021 All Rights Reserved.</span>
</footer>
</body>
</html>
```